Trading company need to develop packaging design for a new nuts brand.

We need a packaging design for a new nuts brand.
- Packaging format - doypack packaging with zip lock 150 g - 150x220mm
- Product line will include all possible types of nuts. We would like to take a pistachio like an exampl for developing design.
- The main task is to connect the whole concept to the Verdalo character /hero (Example of the image is in Uploaded files, but you don't need to use it)
- In design we expect modern, creative and non-standard solutions, we focus on minimalism
- Packaging mustn’t be transparent or craft
- The future product will be a premium segment
- We expect front and back design of packaging
- Our competitors: Vortan and Haldmoller (Examples of competitors' packaging, I will attach in Uploaded files)
- Future brand would be sold in different countries therefore the design must be universal, not connect to any region, country or place of nuts growth.

```html
<!DOCTYPE html>
<html lang="en">
<head>
<meta charset="utf-8">
<title>Verdalo Pistachio Pouch – Front</title>
<link rel="stylesheet" href="https://fonts.googleapis.com/css2?family=Varela+Round&display=swap">
<style>
  :root {
    --backdrop: #cbbb99;
    --mint-light: #bfe6e3;
    --mint: #a9dcdc;
    --cream-glow: #f6f3d6;
    --sun-yellow: #f8ec68;
    --ink-blue: #3346a3;
    --rose: #e2a3a3;
    --rose-deep: #d48f92;
    --rose-light: #f7bcbc;
    --gold-a: #d6bb84;
    --gold-b: #fbf4d8;
    --paper-white: #fbfbfa;
    --label-white: #f4ecec;
    --passion-rose: #c9787a;
    --badge-teal: #37aebd;
    --bowl-brown: #7a4430;
    --nut-cream: #e6d3ad;
  }
  * { margin: 0; padding: 0; box-sizing: border-box; }
  html, body {
    width: 1200px; height: 800px; overflow: hidden;
    background: var(--backdrop);
    font-family: "Varela Round", sans-serif;
  }
  .canvas { position: relative; width: 1200px; height: 800px; }

  .pouch {
    position: absolute; left: 356px; top: 40px;
    width: 488px; height: 720px;
    border-radius: 18px 18px 12px 12px;
    overflow: hidden;
    background: var(--paper-white);
  }
  .pouch__pattern {
    position: absolute; left: 0; top: 0; width: 100%; height: 557px;
    background:
      radial-gradient(ellipse 180px 320px at 244px 200px, var(--cream-glow), transparent 75%),
      linear-gradient(90deg, var(--mint) 0%, var(--mint-light) 40%, var(--mint-light) 60%, var(--mint) 100%);
  }
  .pouch__notch {
    position: absolute; top: 100px; width: 8px; height: 8px;
    border-radius: 50%; background: var(--backdrop);
  }
  .pouch__notch--left { left: -4px; }
  .pouch__notch--right { right: -4px; }

  .brand {
    position: absolute; left: 164px; top: 67px;
    width: 160px; height: 160px; border-radius: 50%;
    background: var(--sun-yellow);
    display: flex; align-items: center; justify-content: center;
  }
  .brand__name {
    color: var(--ink-blue); font-size: 34px; letter-spacing: 0.5px;
  }

  .label {
    position: absolute; left: 109px; top: 316px;
    width: 269px; height: 281px;
    border-radius: 6px; overflow: hidden;
    background: linear-gradient(100deg, var(--rose-deep) 0%, var(--rose) 55%, var(--rose-light) 100%);
  }
  .label__band {
    position: absolute; left: 0; bottom: 0; width: 100%; height: 38px;
    background: linear-gradient(90deg, var(--gold-a), var(--gold-b));
  }
  .label__product {
    position: absolute; left: 18px; top: 98px;
    color: var(--label-white); font-size: 35px; letter-spacing: 1px;
  }
  .label__weight {
    position: absolute; left: 22px; top: 147px;
    color: var(--label-white); font-size: 12px;
  }

  .product-photo {
    position: absolute; left: 171px; top: 252px;
    width: 138px; height: 138px; border-radius: 50%;
    background: radial-gradient(circle, var(--nut-cream) 0%, var(--nut-cream) 62%, var(--bowl-brown) 68%, var(--bowl-brown) 100%);
  }

  .tagline {
    position: absolute; left: 27px; top: 620px;
    color: var(--passion-rose); font-size: 16px; line-height: 20px;
    text-transform: uppercase;
  }
  .certification {
    position: absolute; left: 392px; top: 608px;
  }
</style>
</head>
<body>
<div class="canvas">
  <div class="pouch">
    <div class="pouch__pattern" role="img" aria-label="Repeating pattern of hand-drawn teal pistachio outlines on a mint background"></div>
    <span class="pouch__notch pouch__notch--left"></span>
    <span class="pouch__notch pouch__notch--right"></span>

    <div class="brand">
      <span class="brand__name">Verdalo</span>
    </div>

    <div class="label">
      <p class="label__product">PISTACHIO</p>
      <p class="label__weight">Net Wt. 150g</p>
      <div class="label__band"></div>
    </div>

    <div class="product-photo" role="img" aria-label="Photo of a brown bowl filled with roasted pistachios, seen from above"></div>

    <p class="tagline">Made<br>with<br>passion</p>

    <svg class="certification" width="54" height="60" viewBox="0 0 54 60" aria-hidden="true">
      <circle cx="27" cy="24" r="20" fill="none" stroke="var(--badge-teal)" stroke-width="2"/>
      <path d="M16 40 L10 56 L18 52 L22 58 L27 44 M38 40 L44 56 L36 52 L32 58 L27 44" fill="none" stroke="var(--badge-teal)" stroke-width="2" stroke-linejoin="round"/>
    </svg>
  </div>
</div>
</body>
</html>
```